Email Banner/Facebook post banner

Hi there, we're after a set of sleek Email banners (1200 x 600 px) in jpg and png to use for a HVAC heating and cooling system. We work with Korvo, Tessle, Palvor, Kanemoro and Harukawa HVAC brands and we want to create a series of eDM campaigns.

The messages/headlines are around these: 1. Looking to reduce your gas bills significantly? Harness the efficient power of a HVAC split system to keep your home comfortable all year round! 2. Looking for a powerful heating solution to replace your gas? Access up to $8,000 rebates through the Halden Power Renewal Program! 3. Pay as little as $1,499* for a 3-head split system! Normally $9,900. Available to valued existing customers of Korvane Energy. Hurry!

We want to create at least 5 eDM banner plus 3-4 Facebook post artwork based on the same designs as the eDM. You can just grab images online. We have a design guide too if you can incorporate this. Please quote me a good price.

```html
<!DOCTYPE html>
<html lang="en">
<head>
<meta charset="utf-8">
<title>Korvane Energy – Loyalty Special Offer</title>
<link rel="stylesheet" href="https://fonts.googleapis.com/css2?family=Mulish:wght@400;500;600;700&display=swap">
<style>
  :root {
    --brand-green: #2a6b33;
    --ink: #2f2f2f;
    --ink-soft: #444444;
    --panel-grey: #f5f5f5;
    --card-border: #e4e4e4;
    --white: #ffffff;
    --icon-tint: #e3efe4;
    --hero-left: #3c3d3f;
    --hero-mid: #8d8f92;
    --hero-right: #c9cacc;
  }
  * { box-sizing: border-box; margin: 0; padding: 0; }
  html, body { width: 1200px; height: 2457px; overflow: hidden; }
  body { font-family: "Mulish", Arial, sans-serif; color: var(--ink); background: var(--white); }
  .email { position: relative; width: 1200px; height: 2457px; overflow: hidden; }

  /* Wordmark: plain name, one colour, one weight */
  .wordmark { position: absolute; color: var(--white); font-size: 40px; font-weight: 600; line-height: 1; white-space: nowrap; }

  /* Hero */
  .hero { position: absolute; left: 0; top: 0; width: 1200px; height: 618px; }
  .hero-photo {
    position: absolute; inset: 0;
    background: linear-gradient(90deg, var(--hero-left) 0%, #6a6b6e 30%, var(--hero-mid) 55%, var(--hero-right) 100%);
  }
  .hero .wordmark { left: 68px; top: 78px; }
  .hero-title { position: absolute; left: 64px; top: 228px; font-size: 37px; font-weight: 600; color: var(--white); white-space: nowrap; }
  .hero-copy { position: absolute; left: 67px; top: 278px; font-size: 24px; font-weight: 700; line-height: 32px; color: var(--white); white-space: nowrap; }
  .hero-price { position: absolute; left: 64px; top: 378px; font-size: 38px; font-weight: 700; color: var(--white); }
  .btn {
    position: absolute; display: flex; align-items: center; justify-content: center;
    background: var(--brand-green); color: var(--white); border-radius: 40px; font-weight: 600; text-decoration: none; white-space: nowrap;
  }
  .btn-contact { left: 66px; top: 443px; width: 198px; height: 61px; font-size: 24px; }

  /* Greeting */
  .greeting { position: absolute; left: 0; top: 618px; width: 1200px; height: 460px; background: var(--white); }
  .greeting-hello { position: absolute; left: 70px; top: 80px; font-size: 30px; font-weight: 600; color: var(--brand-green); }
  .greeting-offer { position: absolute; left: 70px; top: 153px; font-size: 37px; font-weight: 600; line-height: 52px; color: var(--ink); white-space: nowrap; }
  .greeting-offer span { color: var(--brand-green); }
  .btn-interest { left: 66px; top: 283px; width: 370px; height: 74px; font-size: 31px; }
  .megaphone { position: absolute; left: 836px; top: 118px; width: 250px; height: 226px; border-radius: 50%;
    background: radial-gradient(circle at 45% 50%, #e9ece9 0%, #c7d8c9 45%, #ffffff 72%); }

  /* Why upgrade */
  .reasons { position: absolute; left: 0; top: 1078px; width: 1200px; height: 642px; background: var(--panel-grey); }
  .reasons-title { position: absolute; left: 0; top: 102px; width: 1200px; text-align: center; font-size: 42px; font-weight: 600; color: var(--brand-green); }
  .reason-card { position: absolute; top: 185px; width: 327px; height: 336px; background: var(--white); border: 2px solid var(--card-border); }
  .reason-card:nth-of-type(1) { left: 66px; }
  .reason-card:nth-of-type(2) { left: 437px; }
  .reason-card:nth-of-type(3) { left: 808px; }
  .reason-icon { position: absolute; left: 22px; top: 22px; width: 68px; height: 68px; border-radius: 50%; background: var(--icon-tint); }
  .reason-text { position: absolute; left: 26px; top: 138px; width: 292px; font-size: 28px; line-height: 42px; color: var(--ink-soft); }
  .reason-card:nth-of-type(3) .reason-text { left: 34px; }
  .reason-text strong { font-weight: 700; color: var(--ink); }
  .reason-text em { font-style: normal; color: var(--brand-green); }

  /* Closing call to action */
  .closing { position: absolute; left: 0; top: 1720px; width: 1200px; height: 416px; background: var(--white); }
  .closing-text { position: absolute; left: 0; top: 103px; width: 1200px; text-align: center; font-size: 35px; line-height: 54px; color: var(--brand-green); }
  .btn-closing { left: 404px; top: 231px; width: 370px; height: 76px; font-size: 31px; }

  /* Footer */
  .footer { position: absolute; left: 0; top: 2136px; width: 1200px; height: 321px; background: var(--brand-green); }
  .footer-notes { position: absolute; left: 0; top: 50px; width: 1200px; text-align: center; font-size: 24px; line-height: 41px; color: var(--white); }
  .footer .wordmark { left: 68px; top: 208px; }
  .social { position: absolute; top: 197px; width: 63px; height: 63px; border-radius: 50%; border: 4px solid var(--white); }
  .social-1 { left: 836px; }
  .social-2 { left: 914px; }
  .social-3 { left: 991px; }
  .social-4 { left: 1070px; }
</style>
</head>
<body>
<main class="email">

  <section class="hero">
    <div class="hero-photo" role="img" aria-label="Photo of a couple in a bright living room pointing a remote at a wall-mounted split system air conditioner"></div>
    <div class="wordmark">Korvane Energy</div>
    <h1 class="hero-title">Upgrade Your Old Gas Heating</h1>
    <p class="hero-copy">Unlock Up To $8,000 in Rebates and as a<br>Valued Customer of Korvane, Pay From<br>&#x1F447; for a Multi-Head Split System</p>
    <p class="hero-price">$1,799</p>
    <a class="btn btn-contact" href="#">Contact Us</a>
  </section>

  <section class="greeting">
    <p class="greeting-hello">Good Afternoon</p>
    <h2 class="greeting-offer">Upgrade Your Comfort And Save Big With<br>Our Loyalty Special Offer $ 1799<span>*</span></h2>
    <a class="btn btn-interest" href="#">Yes I’m Insterested</a>
    <div class="megaphone" role="img" aria-label="Illustration of a green and white megaphone announcing the offer"></div>
  </section>

  <section class="reasons">
    <h2 class="reasons-title">Why Upgrade Now?</h2>
    <article class="reason-card">
      <div class="reason-icon" role="img" aria-label="Money bag in hand icon"></div>
      <p class="reason-text"><strong>Unlock upto $8000</strong> in government rebates to swith from gas heating</p>
    </article>
    <article class="reason-card">
      <div class="reason-icon" role="img" aria-label="Piggy bank savings icon"></div>
      <p class="reason-text"><strong>Avoid paying nearly $3500</strong> annually on heating and coolng costs<em>**</em></p>
    </article>
    <article class="reason-card">
      <div class="reason-icon" role="img" aria-label="Carbon reduction cloud icon"></div>
      <p class="reason-text"><strong>Reduce your carbon footprint</strong> with an<br>all&#8209;electric solution</p>
    </article>
  </section>

  <section class="closing">
    <p class="closing-text">Dont’s Miss This Chance To Upgrade Your Home Comfort At An<br>Unbeatable Price - And Hurry, Special Offer Ends Soon!</p>
    <a class="btn btn-closing" href="#">Yes I’m Insterested</a>
  </section>

  <footer class="footer">
    <p class="footer-notes">*Terms and conditions apply, and special offer is valid until 30.04.2025<br>**Saving based on average household engery costs</p>
    <div class="wordmark">Korvane Energy</div>
    <a class="social social-1" href="#" aria-label="Social profile 1"></a>
    <a class="social social-2" href="#" aria-label="Social profile 2"></a>
    <a class="social social-3" href="#" aria-label="Social profile 3"></a>
    <a class="social social-4" href="#" aria-label="Social profile 4"></a>
  </footer>

</main>
</body>
</html>
```